Buch-/eBook-Cover für Geschichte zum Pride auf Gran Canaria
Zielgruppe
Zielgruppe: Reisefreudige junge schwule Männer
Aufgabenstellung
Die Geschichte spielt zum Pride auf Gran Canaria. Es geht um vier Freunde die dort ihre Ferien verbingen.
Ich stelle mir vor, dass auf dem Cover die Regenbogenflagge ist, Strand, Meer, keine Menschen und ein fetter Schriftzug mit dem Titel #TorvilenaGlanz. Daneben sollte kleiner mein Name Ferdinand zu Brakwede stehen. Das Cover kann aber auch gern wie ein Partyflyer designt sein und der Titel wie ein Logo wirken.
Bin aber für alternativen offen.

```html
<!DOCTYPE html>
<html lang="de">
<head>
<meta charset="utf-8">
<title>#TorvilenaGlanz – Buchcover</title>
<link rel="stylesheet" href="https://fonts.googleapis.com/css2?family=Lilita+One&family=Roboto:wght@400&display=swap">
<style>
  :root {
    --stage: #f3f1f4;
    --sky-top: #a7c9e6;
    --sky-haze: #ece4ee;
    --sea: #6e9dc2;
    --sand-light: #e6d2ad;
    --sand-deep: #cfb48c;
    --author: #2f3f8f;
    --rb-purple: #5a2c8d;
    --rb-blue: #2b5fb6;
    --rb-green: #38a247;
    --rb-yellow: #f1c21b;
    --rb-orange: #ec7a1e;
    --rb-red: #c41f2b;
    --title-rim: #ffffff;
  }
  html, body {
    margin: 0;
    width: 1200px;
    height: 846px;
    overflow: hidden;
    background: var(--stage);
  }
  .stage {
    position: relative;
    width: 1200px;
    height: 846px;
  }
  .book-cover {
    position: absolute;
    left: 348px;
    top: 58px;
    width: 504px;
    height: 730px;
    box-shadow: 0 6px 18px rgba(0,0,0,0.18);
  }
  .book-cover svg { display: block; }
  .rainbow-beam { opacity: 0.42; }
  .cover-title {
    font-family: "Lilita One", "Arial Black", sans-serif;
    font-size: 92px;
    paint-order: stroke fill;
    stroke: var(--title-rim);
    stroke-width: 12px;
    stroke-linejoin: round;
  }
  .cover-author {
    font-family: "Roboto", Arial, sans-serif;
    font-size: 17px;
    fill: var(--author);
  }
</style>
</head>
<body>
<main class="stage">
  <section class="book-cover" aria-label="Buchcover #TorvilenaGlanz">
    <svg width="504" height="730" viewBox="0 0 504 730" xmlns="http://www.w3.org/2000/svg">
      <defs>
        <linearGradient id="scene-tones" x1="0" y1="0" x2="0" y2="1">
          <stop offset="0" stop-color="var(--sky-top)"/>
          <stop offset="0.45" stop-color="var(--sky-haze)"/>
          <stop offset="0.565" stop-color="#c9d8ea"/>
          <stop offset="0.59" stop-color="var(--sea)"/>
          <stop offset="0.635" stop-color="#b9c3c2"/>
          <stop offset="0.68" stop-color="var(--sand-deep)"/>
          <stop offset="1" stop-color="var(--sand-light)"/>
        </linearGradient>
        <linearGradient id="beam-ink" x1="0" y1="1" x2="1" y2="0">
          <stop offset="0" stop-color="var(--rb-purple)"/>
          <stop offset="0.2" stop-color="var(--rb-blue)"/>
          <stop offset="0.4" stop-color="var(--rb-green)"/>
          <stop offset="0.6" stop-color="var(--rb-yellow)"/>
          <stop offset="0.8" stop-color="var(--rb-orange)"/>
          <stop offset="1" stop-color="var(--rb-red)"/>
        </linearGradient>
        <linearGradient id="rainbow-ink" x1="0" y1="0" x2="1" y2="0.25">
          <stop offset="0" stop-color="var(--rb-purple)"/>
          <stop offset="0.2" stop-color="var(--rb-blue)"/>
          <stop offset="0.42" stop-color="var(--rb-green)"/>
          <stop offset="0.62" stop-color="var(--rb-yellow)"/>
          <stop offset="0.8" stop-color="var(--rb-orange)"/>
          <stop offset="1" stop-color="var(--rb-red)"/>
        </linearGradient>
        <linearGradient id="rainbow-ink-short" x1="0" y1="0" x2="0.6" y2="1">
          <stop offset="0" stop-color="var(--rb-blue)"/>
          <stop offset="0.45" stop-color="var(--rb-green)"/>
          <stop offset="1" stop-color="var(--rb-yellow)"/>
        </linearGradient>
        <linearGradient id="star-ink" x1="0" y1="1" x2="1" y2="0">
          <stop offset="0" stop-color="var(--rb-purple)"/>
          <stop offset="0.25" stop-color="var(--rb-blue)"/>
          <stop offset="0.45" stop-color="var(--rb-green)"/>
          <stop offset="0.65" stop-color="var(--rb-yellow)"/>
          <stop offset="0.85" stop-color="var(--rb-orange)"/>
          <stop offset="1" stop-color="var(--rb-red)"/>
        </linearGradient>
      </defs>

      <rect class="cover-photo" x="0" y="0" width="504" height="730" fill="url(#scene-tones)"
            role="img" aria-label="Foto: Sanddünen am Strand mit Meer und Himmel"/>

      <polygon class="rainbow-beam" points="170,0 250,0 504,300 504,400" fill="url(#beam-ink)"/>

      <path class="rainbow-star rainbow-star--large" fill="url(#star-ink)"
            transform="translate(352 160) rotate(8) scale(56)"
            d="M0,-1 L0.247,-0.34 L0.951,-0.309 L0.399,0.13 L0.588,0.809 L0,0.42 L-0.588,0.809 L-0.399,0.13 L-0.951,-0.309 L-0.247,-0.34Z"/>
      <path class="rainbow-star rainbow-star--small" fill="url(#star-ink)"
            transform="translate(106 384) rotate(-6) scale(30)"
            d="M0,-1 L0.247,-0.34 L0.951,-0.309 L0.399,0.13 L0.588,0.809 L0,0.42 L-0.588,0.809 L-0.399,0.13 L-0.951,-0.309 L-0.247,-0.34Z"/>

      <text class="cover-title" x="24" y="228" textLength="448" lengthAdjust="spacingAndGlyphs"
            fill="url(#rainbow-ink)" transform="rotate(-4 250 210)">#Torvilena</text>
      <text class="cover-title" x="70" y="326" textLength="170" lengthAdjust="spacingAndGlyphs"
            fill="url(#rainbow-ink-short)" transform="rotate(5 155 300)">Glanz</text>

      <text class="cover-author" x="462" y="406" text-anchor="end">Ferdinand zu Brakwede</text>
    </svg>
  </section>
</main>
</body>
</html>
```